Harbor Ledger Funds Bus card and Logo

I need a logo design and Bus card design. The fund focuses on evaluating and investing in minerals (sub-surface rights) and real estate.

Harbor ledger refers to a book of knowledge that each plebe gets when entering the Kelmont Marine Academy (my alma mater)

Target Market(s)

Investors and financial advisors

Contact Information for Business Card

Simple - perhaps a logo with a theme on book of knowledge

Logo Text

Ex Scientia Imperium

Font styles to use
Serif
Sans Serif

Colors

Designer to choose colors to be used in the design.

Requirements
Must have
• memorable logo that is relatively simple

```html
<!DOCTYPE html>
<html lang="en">
<head>
<meta charset="utf-8">
<title>Harbor Ledger Funds – Business Card</title>
<link rel="stylesheet" href="https://fonts.googleapis.com/css2?family=Questrial&family=Montserrat:wght@600;700&display=swap">
<style>
  :root {
    --backdrop: #828386;
    --card-light: #ffffff;
    --card-dark: #000000;
    --ink-grey: #7b7b7d;
    --ink-white: #ffffff;
    --rule-grey: #8a8a8a;
    --rule-white: #e6e6e6;
  }
  * { margin: 0; padding: 0; box-sizing: border-box; }
  html, body { width: 1200px; height: 1000px; overflow: hidden; }
  body { background: var(--backdrop); position: relative; font-family: "Questrial", sans-serif; }

  .card {
    position: absolute; left: 257px; width: 686px; height: 392px;
    box-shadow: 0 24px 40px rgba(0,0,0,0.22);
  }
  .card--light { top: 88px; background: var(--card-light); color: var(--ink-grey); --rule: var(--rule-grey); }
  .card--dark { top: 534px; background: var(--card-dark); color: var(--ink-white); --rule: var(--rule-white); }

  .brand {
    position: absolute; left: 48px; top: 105px; width: 240px;
    text-align: center;
  }
  .brand__mark {
    display: block; margin: 0 auto 14px; width: 72px; height: 72px;
    border: 3px solid currentColor; border-radius: 50%;
  }
  .brand__name {
    font-size: 27px; letter-spacing: 1.5px; line-height: 1;
  }
  .brand__sub {
    margin-top: 10px; font-size: 17px; letter-spacing: 3px; line-height: 1;
  }

  .divider {
    position: absolute; left: 313px; top: 68px; width: 2px; height: 256px;
    background: var(--rule);
  }

  .holder-name {
    position: absolute; left: 350px; top: 64px;
    font-family: "Montserrat", sans-serif; font-weight: 700;
    font-size: 24px; letter-spacing: 3.5px;
  }

  .contacts { position: absolute; left: 350px; top: 213px; list-style: none; }
  .contacts li {
    display: flex; align-items: center; height: 41px;
    font-size: 21px;
  }
  .contacts li.phone { font-family: "Montserrat", sans-serif; font-weight: 600; font-size: 20px; }
  .contacts svg { width: 22px; height: 22px; margin-right: 11px; flex: none; }
</style>
</head>
<body>

<section class="card card--light">
  <div class="brand">
    <span class="brand__mark"></span>
    <div class="brand__name">HARBOR LEDGER</div>
    <div class="brand__sub">FUNDS</div>
  </div>
  <div class="divider"></div>
  <div class="holder-name">NAME</div>
  <ul class="contacts">
    <li class="phone">
      <svg viewBox="0 0 24 24" fill="currentColor"><path d="M6.6 10.8a15.1 15.1 0 0 0 6.6 6.6l2.2-2.2c.3-.3.7-.4 1-.2 1.1.4 2.3.6 3.6.6.6 0 1 .4 1 1V20c0 .6-.4 1-1 1A17 17 0 0 1 3 4c0-.6.4-1 1-1h3.5c.6 0 1 .4 1 1 0 1.3.2 2.5.6 3.6.1.3 0 .7-.2 1z"/></svg>
      +00 00000000
    </li>
    <li>
      <svg viewBox="0 0 24 24" fill="currentColor"><path d="M2 5h20v14H2z M3.5 6.5 12 12.5l8.5-6" stroke="var(--card-light)" stroke-width="1.4"/></svg>
      harborledger@.....com
    </li>
    <li>
      <svg viewBox="0 0 24 24" fill="none" stroke="currentColor" stroke-width="1.8"><circle cx="12" cy="12" r="10"/><ellipse cx="12" cy="12" rx="4.5" ry="10"/><path d="M2 12h20M4 7h16M4 17h16"/></svg>
      www.harborledger.com
    </li>
  </ul>
</section>

<section class="card card--dark">
  <div class="brand">
    <span class="brand__mark"></span>
    <div class="brand__name">HARBOR LEDGER</div>
    <div class="brand__sub">FUNDS</div>
  </div>
  <div class="divider"></div>
  <div class="holder-name">NAME</div>
  <ul class="contacts">
    <li class="phone">
      <svg viewBox="0 0 24 24" fill="currentColor"><path d="M6.6 10.8a15.1 15.1 0 0 0 6.6 6.6l2.2-2.2c.3-.3.7-.4 1-.2 1.1.4 2.3.6 3.6.6.6 0 1 .4 1 1V20c0 .6-.4 1-1 1A17 17 0 0 1 3 4c0-.6.4-1 1-1h3.5c.6 0 1 .4 1 1 0 1.3.2 2.5.6 3.6.1.3 0 .7-.2 1z"/></svg>
      +00 00000000
    </li>
    <li>
      <svg viewBox="0 0 24 24" fill="currentColor"><path d="M2 5h20v14H2z M3.5 6.5 12 12.5l8.5-6" stroke="var(--card-dark)" stroke-width="1.4"/></svg>
      harborledger@.....com
    </li>
    <li>
      <svg viewBox="0 0 24 24" fill="none" stroke="currentColor" stroke-width="1.8"><circle cx="12" cy="12" r="10"/><ellipse cx="12" cy="12" rx="4.5" ry="10"/><path d="M2 12h20M4 7h16M4 17h16"/></svg>
      www.harborledger.com
    </li>
  </ul>
</section>

</body>
</html>
```